Online interactive tutorial for year 2 to year 12 students in Australia

Website design for a new online tutorial for year 2 to year 12 students in Australia.

- The tutorial will be conducted via live webcam and within a dedicated interactive space
- The tutorial will be provided by high scoring undergraduates studying in top Australian universities.
- The tutors will be going through interviews & assessments & only top students are allowed to apply.
- Parents will do search and select tutor and have short 15 mins video interaction with potential tutors before booking them for their children for tutoring.
- hourly cost of booking (no monthly subscription or no hour limits)
- Tutors will have their own profile

Please see the attached for detailed page functionality.

The look and feel of the design must consider the following:
- must be educational but not dull and should stand out
- must appeal to younger generation - tutees (8-18 years), tutors (19-25), parents (30-50).
- Ideas for Logos (brivora.com.au but not confirmed)

Target Market(s)

tutees (8-18 years), tutors (19-25 years), parents (30-50 years).

Industry/Entity Type

Education

Coding

Coded - Design and coding required

Number of Pages Required

5+ page

Font styles to use
Serif

Requirements
Must have
• The look and feel of the design must consider the following:
• - must be educational but not dull and should stand out
• - must appeal to younger generation - tutees (8-18 years), tutors (19-25), parents (30-50).
Should not have
• Dullness

```html
<!DOCTYPE html>
<html lang="en">
<head>
<meta charset="utf-8">
<title>Brivora – Online Tutoring</title>
<link href="https://fonts.googleapis.com/css2?family=Montserrat:wght@400;500;600;700&display=swap" rel="stylesheet">
<style>
:root{
  --navy:#0d4c9c;
  --orange:#ff6a0d;
  --yellow:#ffb10a;
  --team-blue:#2d6fbf;
  --ink:#222222;
  --muted:#555555;
  --light:#efefef;
  --dark:#2a2b2d;
  --darker:#111111;
  --white:#ffffff;
}
*{margin:0;padding:0;box-sizing:border-box}
html,body{width:1200px;height:3197px;overflow:hidden}
body{font-family:'Montserrat',sans-serif;color:var(--ink);background:var(--white);position:relative}
section,header,footer{position:absolute;left:0;width:1200px}
.abs{position:absolute}
.btn{position:absolute;height:34px;border-radius:17px;color:var(--white);font-size:13px;font-weight:500;display:flex;align-items:center;justify-content:center}
.btn-orange{background:var(--orange)}
.btn-yellow{background:var(--yellow)}
.center{text-align:center;left:0;width:1200px}
.section-title{font-size:27px;font-weight:500;letter-spacing:.5px}

/* hero */
.hero{top:0;height:612px;background:linear-gradient(100deg,#6d6a6a 0%,#9a8f88 35%,#b9aca2 55%,#5f5550 80%,#3c3836 100%)}
.hero-shade{position:absolute;inset:0;background:rgba(20,20,30,.35)}
.logo{left:155px;top:22px;font-size:38px;font-weight:600;color:var(--white)}
.login{left:823px;top:10px;width:150px;height:33px;border-radius:17px;background:var(--navy);color:var(--white);font-size:12px;font-weight:500;display:flex;align-items:center;justify-content:center;gap:8px}
.menu{left:988px;top:15px;color:var(--white);font-size:12px;display:flex;align-items:center;gap:12px}
.hero-title{top:398px;font-size:29px;font-weight:500;color:var(--white);line-height:37px}
.dots{display:flex;gap:14px;justify-content:center}
.dot{width:7px;height:7px;border-radius:50%;background:rgba(255,255,255,.55)}
.dot.on{background:var(--white)}

/* welcome */
.welcome{top:612px;height:415px;background:var(--white)}
.welcome .section-title{top:22px}
.lead{top:67px;font-size:12px;color:var(--ink)}
.feature{position:absolute;top:117px;width:200px;text-align:center}
.feature-icon{width:68px;height:68px;border-radius:50%;background:var(--navy);margin:0 auto;display:flex;align-items:center;justify-content:center}
.feature h3{margin-top:26px;font-size:11px;font-weight:700}
.feature p{margin-top:12px;font-size:10px;line-height:14px;color:var(--muted)}

/* videos */
.videos{top:1027px;height:337px;background:var(--light)}
.videos .section-title{top:20px}
.video{position:absolute;top:75px;width:226px}
.video-thumb{height:172px;display:flex;align-items:center;justify-content:center;border:2px solid var(--white)}
.play{width:40px;height:40px;border-radius:50%;background:#111;display:flex;align-items:center;justify-content:center}
.video h3{margin-top:12px;text-align:center;font-size:15px;font-weight:500}

/* feedback */
.feedback{top:1364px;height:439px;background:linear-gradient(120deg,#2c3340 0%,#4c4a52 40%,#6a5560 60%,#3a3a48 100%)}
.feedback-shade{position:absolute;inset:0;background:rgba(10,10,20,.35)}
.feedback .section-title{top:32px;color:var(--white)}
.quote{position:absolute;top:192px;width:267px;height:112px;background:var(--white)}
.quote::after{content:"";position:absolute;right:30px;bottom:-14px;border-left:14px solid transparent;border-top:14px solid var(--white)}
.avatar{position:absolute;left:15px;top:20px;width:64px;height:64px;border-radius:50%;background:linear-gradient(#c49a86,#7a5446);border:3px solid var(--white);box-shadow:0 0 0 1px #ccc}
.quote p{position:absolute;left:92px;top:20px;width:160px;font-size:10.5px;line-height:14px;color:#777}
.stars{position:absolute;top:318px;display:flex;gap:6px}
.who{position:absolute;top:316px;color:var(--white);font-size:12px;font-weight:700}
.who span{display:block;font-size:8px;font-weight:400;margin-top:2px}

/* about */
.about{top:1803px;height:356px;background:var(--white)}
.laptop-screen{left:209px;top:68px;width:294px;height:184px;background:#1a1a1a;border-radius:8px;padding:10px}
.screen-view{width:100%;height:100%;background:linear-gradient(90deg,#3b3b44,#8b6e60,#3b3b44)}
.laptop-base{left:188px;top:252px;width:336px;height:10px;background:linear-gradient(#d9d9d9,#9a9a9a);border-radius:0 0 12px 12px}
.about h2{left:595px;top:60px;font-size:27px;font-weight:500}
.about p{left:595px;top:112px;width:453px;font-size:10.5px;line-height:16.5px;color:var(--ink)}

/* team */
.team{top:2159px;height:441px;background:linear-gradient(90deg,#2b69b8,#3b7cc6 50%,#2a63ad)}
.team .section-title{top:56px;color:var(--white)}
.team-sub{top:96px;font-size:14px;color:var(--white)}
.featured{left:168px;top:111px;width:184px;height:294px;background:var(--orange)}
.tutor{position:absolute;top:147px;width:132px;height:132px;border-radius:50%;border:4px solid var(--white);background:linear-gradient(#d9b7a3,#6b4a3e)}
.featured-name{left:168px;top:290px;width:184px;text-align:center;color:var(--white)}
.featured-name strong{display:block;font-size:15px;font-weight:600}
.featured-name span{display:block;font-size:10px;margin-top:6px;line-height:14px;font-weight:600}
.more-btn{left:214px;top:352px;width:92px;height:22px;border:1px solid var(--white);border-radius:11px;color:var(--white);font-size:8px;display:flex;align-items:center;justify-content:center}
.motto{left:400px;top:312px;width:400px;text-align:center;color:var(--white);font-size:14px;font-weight:500}
.learn{left:541px;top:356px;width:118px;height:37px;border:2px solid var(--white);border-radius:19px;color:var(--white);font-size:12px;display:flex;align-items:center;justify-content:center}

/* contact */
.contact{top:2600px;height:545px;background:linear-gradient(180deg,#2e2f31,#262729)}
.contact .section-title{top:62px;color:var(--white)}
.field{position:absolute;left:213px;width:275px;height:32px;background:var(--white);font-size:11px;padding:9px 12px;color:var(--ink)}
.submit{left:213px;top:356px;width:275px;height:34px;background:var(--yellow);color:var(--white);font-size:18px;display:flex;align-items:center;justify-content:center}
.addr-title{left:575px;top:150px;color:var(--white);font-size:18px;font-weight:600}
.addr-row{position:absolute;left:575px;display:flex;gap:14px;color:var(--white);font-size:11px;font-weight:600;line-height:16px}
.call-line{left:575px;top:326px;color:var(--white);font-size:18px;font-weight:600}
.call-num{left:575px;top:356px;color:var(--white);font-size:29px;font-weight:600}
.pay{top:434px;display:flex;gap:8px;justify-content:center}
.pay span{width:34px;height:20px;background:var(--white);border-radius:2px}
.social{top:470px;display:flex;gap:30px;justify-content:center;color:var(--white);font-size:12px;font-weight:600}
.footer-links{top:514px;display:flex;gap:26px;justify-content:center;color:var(--white);font-size:10px}

.copyright{top:3145px;height:52px;background:var(--darker);color:var(--white);font-size:10px;display:flex;align-items:center;justify-content:center}
.copyright em{position:absolute;right:160px;font-style:normal}
</style>
</head>
<body>

<header class="hero">
  <div class="hero-shade" role="img" aria-label="Photo of smiling tutors wearing headsets"></div>
  <div class="abs logo">brivora</div>
  <div class="abs login">
    <svg width="10" height="11" viewBox="0 0 10 11"><circle cx="5" cy="3" r="2.6" fill="#fff"/><path d="M0 11c0-3.5 2.2-5 5-5s5 1.5 5 5z" fill="#fff"/></svg>
    Student Login
  </div>
  <div class="abs menu">Menu
    <svg width="20" height="16" viewBox="0 0 20 16"><rect y="1" width="20" height="2.5" fill="#fff"/><rect y="7" width="20" height="2.5" fill="#fff"/><rect y="13" width="20" height="2.5" fill="#fff"/></svg>
  </div>
  <h1 class="abs center hero-title">We are an online training website for kids<br>from 2 years to 12 years</h1>
  <div class="btn btn-yellow" style="left:409px;top:505px;width:186px">Tutor Registration</div>
  <div class="btn btn-orange" style="left:605px;top:505px;width:188px">Parent Registration</div>
  <div class="abs center dots" style="top:581px">
    <span class="dot"></span><span class="dot"></span><span class="dot"></span><span class="dot on"></span><span class="dot"></span><span class="dot"></span><span class="dot"></span>
  </div>
</header>

<section class="welcome">
  <h2 class="abs center section-title">WELCOME TO BRIVORA</h2>
  <p class="abs center lead">Lorem ipsum dolor sit amet, consectetur adipiscing elit, sed do eiusmod tempor incididunt ut labore et dolore magna aliqua.</p>

  <div class="feature" style="left:177px">
    <div class="feature-icon"><svg width="24" height="24" viewBox="0 0 24 24"><path d="M2 10h4v12H2zM8 22V10l5-8c2 0 3 1 2.5 3L14 9h6c1.5 0 2.5 1.3 2 2.8l-2.5 8.5c-.4 1.1-1.3 1.7-2.4 1.7z" fill="#fff"/></svg></div>
    <h3>GREAT TEACHING METHODS</h3>
    <p>Sed ut perspiciatis unde omnis iste natus error sit voluptatem accusantium doloremque laudantium, totam rem aperiam, eaque ipsa.</p>
  </div>
  <div class="feature" style="left:386px">
    <div class="feature-icon"><svg width="28" height="22" viewBox="0 0 28 22"><circle cx="14" cy="6" r="4" fill="#fff"/><circle cx="5" cy="8" r="3" fill="#fff"/><circle cx="23" cy="8" r="3" fill="#fff"/><path d="M7 20c0-5 3-8 7-8s7 3 7 8zM0 19c0-4 2-6 5-6 1 0 2 .3 2.6.8C6.5 15.3 6 17 6 19zM28 19c0-4-2-6-5-6-1 0-2 .3-2.6.8 1.1 1.5 1.6 3.2 1.6 5.2z" fill="#fff"/></svg></div>
    <h3>PROFESSIONAL TUTORS</h3>
    <p>Sed ut perspiciatis unde omnis iste natus error sit voluptatem accusantium doloremque laudantium, totam rem aperiam, eaque ipsa.</p>
  </div>
  <div class="feature" style="left:603px">
    <div class="feature-icon"><svg width="26" height="26" viewBox="0 0 26 26"><circle cx="13" cy="13" r="12" fill="#fff"/><path d="M7 13.5l4 4 8-9" stroke="#0d4c9c" stroke-width="3" fill="none"/></svg></div>
    <h3>FREE TRIAL LESSONS</h3>
    <p>Sed ut perspiciatis unde omnis iste natus error sit voluptatem accusantium doloremque laudantium, totam rem aperiam, eaque ipsa.</p>
  </div>
  <div class="feature" style="left:823px">
    <div class="feature-icon"><svg width="16" height="26" viewBox="0 0 16 26"><text x="8" y="21" text-anchor="middle" font-family="Montserrat, sans-serif" font-size="22" font-weight="700" fill="#fff">$</text></svg></div>
    <h3>COMPETITIVE PRICES</h3>
    <p>Sed ut perspiciatis unde omnis iste natus error sit voluptatem accusantium doloremque laudantium, totam rem aperiam, eaque ipsa.</p>
  </div>

  <div class="btn btn-orange" style="left:477px;top:345px;width:118px">FREE Trial</div>
  <div class="btn btn-yellow" style="left:605px;top:345px;width:117px">Read More</div>
</section>

<section class="videos">
  <h2 class="abs center section-title">VIDEOS</h2>
  <div class="video" style="left:132px">
    <div class="video-thumb" role="img" aria-label="Child using a tablet for a video lesson" style="background:linear-gradient(135deg,#c9b8a6,#8a9a6c)"><span class="play"><svg width="12" height="14" viewBox="0 0 12 14"><path d="M1 0l11 7-11 7z" fill="#fff"/></svg></span></div>
    <h3>LESSONS PART 1</h3>
  </div>
  <div class="video" style="left:371px">
    <div class="video-thumb" role="img" aria-label="Boy studying with sketched school doodles" style="background:linear-gradient(135deg,#f2f2f2,#d8a468)"><span class="play"><svg width="12" height="14" viewBox="0 0 12 14"><path d="M1 0l11 7-11 7z" fill="#fff"/></svg></span></div>
    <h3>PART2 PACKAGES</h3>
  </div>
  <div class="video" style="left:607px">
    <div class="video-thumb" role="img" aria-label="Tutor helping a boy with homework" style="background:linear-gradient(135deg,#6c6f86,#c79a78)"><span class="play"><svg width="12" height="14" viewBox="0 0 12 14"><path d="M1 0l11 7-11 7z" fill="#fff"/></svg></span></div>
    <h3>2 MONTHS PACKAGES</h3>
  </div>
  <div class="video" style="left:842px">
    <div class="video-thumb" role="img" aria-label="Parent reading with a child at a desk" style="background:linear-gradient(135deg,#e4ddd4,#9c8a78)"><span class="play"><svg width="12" height="14" viewBox="0 0 12 14"><path d="M1 0l11 7-11 7z" fill="#fff"/></svg></span></div>
    <h3>6 MONTHS PACKAGES</h3>
  </div>
</section>

<section class="feedback">
  <div class="feedback-shade" role="img" aria-label="Photo of a student learning on a laptop"></div>
  <h2 class="abs center section-title">FEED BACK</h2>

  <div class="quote" style="left:170px"><div class="avatar" role="img" aria-label="Parent portrait"></div><p>Nor again is there anyone who loves or pursues or desires to obtain pain of itself, because it is pain, but because occasionally circumstances occur</p></div>
  <div class="quote" style="left:465px"><div class="avatar" role="img" aria-label="Parent portrait"></div><p>Nor again is there anyone who loves or pursues or desires to obtain pain of itself, because it is pain, but because occasionally circumstances occur</p></div>
  <div class="quote" style="left:761px"><div class="avatar" role="img" aria-label="Parent portrait"></div><p>Nor again is there anyone who loves or pursues or desires to obtain pain of itself, because it is pain, but because occasionally circumstances occur</p></div>

  <svg width="0" height="0" style="position:absolute"><defs><path id="star" d="M7 0l2.1 4.6 4.9.5-3.7 3.3 1.1 4.9L7 10.8 2.6 13.3l1.1-4.9L0 5.1l4.9-.5z" fill="#fff"/></defs></svg>
  <div class="stars" style="left:174px"><svg width="14" height="14"><use href="#star"/></svg><svg width="14" height="14"><use href="#star"/></svg><svg width="14" height="14"><use href="#star"/></svg><svg width="14" height="14"><use href="#star"/></svg><svg width="14" height="14"><use href="#star"/></svg></div>
  <div class="who" style="left:330px">Ella Marsh<span>CEO - Lorem ipsum</span></div>
  <div class="stars" style="left:469px"><svg width="14" height="14"><use href="#star"/></svg><svg width="14" height="14"><use href="#star"/></svg><svg width="14" height="14"><use href="#star"/></svg><svg width="14" height="14"><use href="#star"/></svg><svg width="14" height="14"><use href="#star"/></svg></div>
  <div class="who" style="left:625px">Ella Marsh<span>CEO - Lorem ipsum</span></div>
  <div class="stars" style="left:765px"><svg width="14" height="14"><use href="#star"/></svg><svg width="14" height="14"><use href="#star"/></svg><svg width="14" height="14"><use href="#star"/></svg><svg width="14" height="14"><use href="#star"/></svg><svg width="14" height="14"><use href="#star"/></svg></div>
  <div class="who" style="left:921px">Ella Marsh<span>CEO - Lorem ipsum</span></div>

  <div class="abs center dots" style="top:398px"><span class="dot"></span><span class="dot on"></span><span class="dot"></span><span class="dot"></span><span class="dot"></span></div>
</section>

<section class="about">
  <div class="abs laptop-screen"><div class="screen-view" role="img" aria-label="Tutor on a live webcam session"></div></div>
  <div class="abs laptop-base"></div>
  <h2 class="abs">WHAT IS BRIVORA TUTOR?</h2>
  <p class="abs">Sed ut perspiciatis unde omnis iste natus error sit voluptatem accusantium doloremque laudantium, totam rem aperiam, eaque ipsa quae ab illo inventore veritatis et quasi architecto beatae vitae dicta sunt explicabo. Nemo enim ipsam voluptatem quia voluptas sit aspernatur aut odit aut fugit, sed quia consequuntur magni dolores eos qui ratione voluptatem sequi nesciunt. Neque porro quisquam est, qui dolorem ipsum quia dolor sit amet, consectetur, adipisci velit, sed quia non numquam eius modi tempora incidunt ut labore et dolore magnam aliquam quaerat voluptatem.</p>
  <div class="btn btn-yellow" style="left:597px;top:2103px;top:300px;width:117px">Read More</div>
</section>

<section class="team">
  <div class="abs" style="inset:0;background:rgba(20,80,170,.25)" role="img" aria-label="Photo of students in a classroom"></div>
  <h2 class="abs center section-title">MEET THE TEAM</h2>
  <p class="abs center team-sub">Tutor Profiles</p>
  <div class="abs featured"></div>
  <div class="tutor" role="img" aria-label="Tutor portrait" style="left:194px"></div>
  <div class="abs featured-name"><strong>Leo Hart</strong><span>Professional - Science Teacher<br>Lorem - ipsum dolor amit</span></div>
  <div class="abs more-btn">More About Me</div>
  <div class="tutor" role="img" aria-label="Tutor portrait" style="left:371px"></div>
  <div class="tutor" role="img" aria-label="Tutor portrait" style="left:548px"></div>
  <div class="tutor" role="img" aria-label="Tutor portrait" style="left:725px"></div>
  <div class="tutor" role="img" aria-label="Tutor portrait" style="left:901px"></div>
  <p class="abs motto">We love what we do and we are good folks too!</p>
  <div class="abs learn">Learn More</div>
</section>

<section class="contact">
  <div class="abs" style="inset:0;background:radial-gradient(circle at 50% 45%,rgba(255,255,255,.05),transparent 60%)" role="img" aria-label="Faint world map background"></div>
  <h2 class="abs center section-title">CONTACT US TODAY</h2>
  <svg class="abs" style="left:540px;top:98px" width="38" height="48" viewBox="0 0 38 48"><path d="M19 0C8.5 0 0 8.2 0 18.5 0 32 19 48 19 48s19-16 19-29.5C38 8.2 29.5 0 19 0z" fill="#7a1f1f"/><circle cx="19" cy="18" r="7" fill="#2a2b2d"/></svg>
  <div class="field" style="top:145px">Name</div>
  <div class="field" style="top:185px">Email</div>
  <div class="field" style="top:226px">Address</div>
  <div class="field" style="top:264px;height:83px">Message</div>
  <div class="abs submit">Submit</div>

  <div class="abs addr-title">Address</div>
  <div class="addr-row" style="top:190px"><svg width="10" height="14" viewBox="0 0 10 14"><path d="M5 0C2.2 0 0 2.2 0 5c0 3.8 5 9 5 9s5-5.2 5-9c0-2.8-2.2-5-5-5z" fill="#fff"/><circle cx="5" cy="5" r="2" fill="#2a2b2d"/></svg><span>Main Store 48 Harlow Street<br>North Carlton</span></div>
  <div class="addr-row" style="top:248px"><svg width="12" height="12" viewBox="0 0 12 12"><path d="M2.5 0L5 3 3.5 4.5c.8 1.7 2.3 3.2 4 4L9 7l3 2.5L10.5 12C5 12 0 7 0 1.5z" fill="#fff"/></svg><span>(03) 5550 1427</span></div>
  <div class="addr-row" style="top:276px"><svg width="12" height="10" viewBox="0 0 12 10"><rect width="12" height="10" fill="#fff"/><path d="M0 0l6 5 6-5" stroke="#2a2b2d" fill="none"/></svg><span>info@brivora.com.au</span></div>
  <div class="abs call-line">If you would rather call, you can reach us at</div>
  <div class="abs call-num">1-800 555 210</div>

  <div class="abs center pay" role="img" aria-label="Accepted payment cards"><span></span><span></span><span></span><span></span><span></span></div>
  <div class="abs center social"><span>Chirp</span><span>Lens</span><span>Linkr</span><span>Wave</span><span>Talk</span></div>
  <nav class="abs center footer-links"><span>Home</span><span>About Us</span><span>Tutor Registration</span><span>Parent Registration</span><span>Student Login</span><span>Note Space</span><span>Tutor Profile</span><span>Scheduler</span><span>Feed back</span><span>Contact</span></nav>
</section>

<footer class="copyright">© All rights reserved 2016. www.brivora.com.au<em>Hi</em></footer>

</body>
</html>
```